Flyer-Design für Kindertagesstätte
Felmriks Spielhafen suchte ein neues Design in der Kategorie Flyer und hat ein Projekt auf grafikwunsch.de gestartet.
Zielgruppe
Wir sind eine Kindertagesstätte und wollen eine Baby-Kind-Spielgruppe jeden Mittwoch in unserer Kita von 09.00 Uhr bis 11.00 Uhr anbieten.
Aufgabenstellung
Unser LOGO muss im Flyer enthalten sein, auf jeden Fall ein Bild wenn möglich mit mehreren Babys/Kleinkindern bis 1,5 Jahre. Wir benötigen den Flyer in DIN lang - bunt - 1 seitig.
Folgender Text sollte enthalten: Baby-Kind-Spielgruppe, jeden mittwoch in unserer Kita 'Felmriks Spielhafen' von 09.00 Uhr bis 11.00 Uhr. Die Spielgruppe wird durch unser ausgebildetes Fachpersonal begleitet.

```html
<!DOCTYPE html>
<html lang="de">
<head>
<meta charset="utf-8">
<title>Felmriks Spielhafen – Baby-Kind Spielgruppe</title>
<link rel="stylesheet" href="https://fonts.googleapis.com/css2?family=Montserrat+Alternates:wght@500;600;700&family=Roboto+Slab:wght@800&display=swap">
<style>
  :root {
    --page: #f4f2ef;
    --flyer-orange: #ee6420;
    --cloud-white: #ffffff;
    --tile-red: #e8582a;
    --tile-green: #8dbb2f;
    --tile-cyan: #1db4e6;
    --tile-mustard: #d5a225;
    --tile-pink: #e43c95;
    --text-light: #ffffff;
  }
  html, body {
    margin: 0;
    padding: 0;
    width: 800px;
    height: 1200px;
    overflow: hidden;
    background: var(--page);
  }
  .flyer {
    position: absolute;
    left: 139px;
    top: 40px;
    width: 522px;
    height: 1120px;
    box-shadow: 0 6px 24px rgba(0,0,0,0.12);
  }
  .flyer svg { display: block; width: 100%; height: 100%; }
  .brand-name {
    font-family: "Montserrat Alternates", sans-serif;
    font-weight: 700;
    fill: var(--flyer-orange);
  }
  .tile-letter {
    font-family: "Roboto Slab", serif;
    font-weight: 800;
    font-size: 58px;
    fill: var(--text-light);
  }
  .subtitle {
    font-family: "Montserrat Alternates", sans-serif;
    font-weight: 600;
    font-size: 31px;
    fill: var(--flyer-orange);
  }
  .info-text {
    font-family: "Montserrat Alternates", sans-serif;
    font-weight: 500;
    font-size: 16.5px;
    fill: var(--text-light);
  }
  .icon { fill: none; stroke: var(--text-light); stroke-width: 3; stroke-linecap: round; stroke-linejoin: round; }
</style>
</head>
<body>
<div class="flyer">
  <svg viewBox="0 0 463 993" xmlns="http://www.w3.org/2000/svg">
    <defs>
      <linearGradient id="photo-top-tones" x1="0" y1="0" x2="1" y2="1">
        <stop offset="0" stop-color="#e9c9a8"/>
        <stop offset="0.45" stop-color="#f3d9a0"/>
        <stop offset="0.75" stop-color="#f1c2b8"/>
        <stop offset="1" stop-color="#a9bfd6"/>
      </linearGradient>
      <linearGradient id="photo-baby-tones" x1="0" y1="0" x2="0" y2="1">
        <stop offset="0" stop-color="#f0d1bd"/>
        <stop offset="0.55" stop-color="#a9cde8"/>
        <stop offset="1" stop-color="#c9a0d8"/>
      </linearGradient>
    </defs>

    <!-- background -->
    <rect class="flyer-bg" width="463" height="993" fill="var(--flyer-orange)"/>

    <!-- group photo -->
    <rect role="img" aria-label="Foto: zwei Kleinkinder spielen mit buntem Holzspielzeug" x="0" y="110" width="463" height="420" fill="url(#photo-top-tones)"/>

    <!-- logo cloud -->
    <g class="logo-cloud" fill="var(--cloud-white)">
      <circle cx="145" cy="118" r="55"/>
      <circle cx="235" cy="88" r="100"/>
      <circle cx="325" cy="118" r="55"/>
      <rect x="145" y="0" width="180" height="120"/>
    </g>
    <g class="brand">
      <circle cx="235" cy="70" r="26" fill="var(--flyer-orange)"/>
      <text class="brand-name" x="235" y="135" text-anchor="middle" font-size="18">Felmriks</text>
      <text class="brand-name" x="235" y="157" text-anchor="middle" font-size="18">Spielhafen</text>
    </g>

    <!-- title cloud -->
    <g class="title-cloud" fill="var(--cloud-white)">
      <rect x="0" y="500" width="463" height="185"/>
      <circle cx="235" cy="505" r="110"/>
      <circle cx="105" cy="545" r="80"/>
      <circle cx="365" cy="545" r="80"/>
      <circle cx="160" cy="680" r="68"/>
      <circle cx="310" cy="680" r="68"/>
      <circle cx="235" cy="690" r="70"/>
    </g>

    <!-- letter tiles -->
    <g class="tiles">
      <g transform="rotate(-3 91 510)">
        <rect x="47" y="466" width="88" height="88" rx="8" fill="var(--tile-red)"/>
        <rect x="54" y="473" width="74" height="74" rx="5" fill="none" stroke="#ffffff" stroke-opacity="0.35" stroke-width="2"/>
        <text class="tile-letter" x="91" y="531" text-anchor="middle">B</text>
      </g>
      <g transform="rotate(-2 184 505)">
        <rect x="140" y="461" width="88" height="88" rx="8" fill="var(--tile-green)"/>
        <rect x="147" y="468" width="74" height="74" rx="5" fill="none" stroke="#ffffff" stroke-opacity="0.35" stroke-width="2"/>
        <text class="tile-letter" x="184" y="526" text-anchor="middle">A</text>
      </g>
      <g transform="rotate(-4 277 500)">
        <rect x="233" y="456" width="88" height="88" rx="8" fill="var(--tile-cyan)"/>
        <rect x="240" y="463" width="74" height="74" rx="5" fill="none" stroke="#ffffff" stroke-opacity="0.35" stroke-width="2"/>
        <text class="tile-letter" x="277" y="521" text-anchor="middle">B</text>
      </g>
      <g transform="rotate(-1 373 498)">
        <rect x="329" y="454" width="88" height="88" rx="8" fill="var(--tile-mustard)"/>
        <rect x="336" y="461" width="74" height="74" rx="5" fill="none" stroke="#ffffff" stroke-opacity="0.35" stroke-width="2"/>
        <text class="tile-letter" x="373" y="519" text-anchor="middle">Y</text>
      </g>
      <g transform="rotate(-2 84 603)">
        <rect x="40" y="559" width="88" height="88" rx="8" fill="var(--tile-mustard)"/>
        <rect x="47" y="566" width="74" height="74" rx="5" fill="none" stroke="#ffffff" stroke-opacity="0.35" stroke-width="2"/>
        <text class="tile-letter" x="84" y="624" text-anchor="middle">K</text>
      </g>
      <rect x="163" y="558" width="32" height="7" rx="2" fill="var(--tile-mustard)"/>
      <g transform="rotate(1 178 618)">
        <rect x="134" y="574" width="88" height="88" rx="8" fill="var(--tile-pink)"/>
        <rect x="141" y="581" width="74" height="74" rx="5" fill="none" stroke="#ffffff" stroke-opacity="0.35" stroke-width="2"/>
        <text class="tile-letter" x="178" y="639" text-anchor="middle">I</text>
      </g>
      <g transform="rotate(-4 271 602)">
        <rect x="227" y="558" width="88" height="88" rx="8" fill="var(--tile-red)"/>
        <rect x="234" y="565" width="74" height="74" rx="5" fill="none" stroke="#ffffff" stroke-opacity="0.35" stroke-width="2"/>
        <text class="tile-letter" x="271" y="623" text-anchor="middle">N</text>
      </g>
      <g transform="rotate(-3 366 592)">
        <rect x="322" y="548" width="88" height="88" rx="8" fill="var(--tile-green)"/>
        <rect x="329" y="555" width="74" height="74" rx="5" fill="none" stroke="#ffffff" stroke-opacity="0.35" stroke-width="2"/>
        <text class="tile-letter" x="366" y="613" text-anchor="middle">D</text>
      </g>
    </g>

    <text class="subtitle" x="235" y="705" text-anchor="middle">Spielgruppe</text>

    <!-- baby photo -->
    <path role="img" aria-label="Foto: Baby spielt mit bunten Bausteinen" d="M330 720 C360 700 420 705 463 730 L463 993 L300 993 C270 960 255 900 270 840 C280 790 295 745 330 720 Z" fill="url(#photo-baby-tones)"/>

    <!-- info list -->
    <g class="info-list">
      <g class="icon-calendar">
        <rect class="icon" x="40" y="782" width="36" height="36" rx="5"/>
        <line class="icon" x1="40" y1="792" x2="76" y2="792"/>
        <line class="icon" x1="50" y1="776" x2="50" y2="786"/>
        <line class="icon" x1="66" y1="776" x2="66" y2="786"/>
        <text x="58" y="813" text-anchor="middle" font-family="Montserrat Alternates, sans-serif" font-weight="700" font-size="14" fill="#ffffff">11</text>
      </g>
      <text class="info-text" x="90" y="796">jeden Mittwoch</text>
      <text class="info-text" x="90" y="816">in unserer Kita</text>

      <path class="icon" d="M58 894 C44 882 36 874 36 864 C36 856 42 851 49 851 C53 851 56 853 58 857 C60 853 63 851 67 851 C74 851 80 856 80 864 C80 874 72 882 58 894 Z"/>
      <text class="info-text" x="90" y="862">durch unser ausge-</text>
      <text class="info-text" x="90" y="882">bildetes Fachperso-</text>
      <text class="info-text" x="90" y="902">nal begleitet</text>

      <g class="icon-clock">
        <circle class="icon" cx="58" cy="952" r="19"/>
        <polyline class="icon" points="58,941 58,953 66,958"/>
      </g>
      <text class="info-text" x="92" y="946">von 09.00 Uhr bis</text>
      <text class="info-text" x="92" y="966">11.00 Uhr</text>
    </g>
  </svg>
</div>
</body>
</html>
```